Road Construction Company needs business cards

We would like a new business card designed for our business.

We're a road construction company based in Qld, Australia.

Can the business card please have the following information on it.

Name: Warren Halbeck
Position: General Manager
Phone: 0472 915 348
Email: Warren.halbeck@tovrin.com.au
Address: 87 Marrow Ave, Pendlebay, QLD, 4023
Website: www.tovrin.com.au

Visually we'd like the card to be professional and simple.

Attached is our logo.

Our website is www.tovrin.com.au

Target Market(s)

Men aged 25-60

Contact Information for Business Card

As listed in project description

Font styles to use
Serif

Requirements
Must have
• Large logo on back of card

```html
<!DOCTYPE html>
<html lang="en">
<head>
<meta charset="utf-8">
<title>Tovrin Road Construction – Business Card</title>
<link rel="stylesheet" href="https://fonts.googleapis.com/css2?family=Open+Sans:wght@400;600;700;800&display=swap">
<style>
  :root {
    --brand-blue: #1456a8;
    --accent-blue: #3a9bd9;
    --card-white: #ffffff;
    --backdrop: #2b2b2e;
    --ink-light: #ffffff;
  }
  * { margin: 0; padding: 0; box-sizing: border-box; }
  html, body { width: 1200px; height: 780px; overflow: hidden; }
  body {
    background: var(--backdrop);
    font-family: "Open Sans", Arial, sans-serif;
    position: relative;
  }
  .card {
    position: absolute;
    top: 235px;
    width: 540px;
    height: 309px;
    overflow: hidden;
  }
  .card-front { left: 40px; background: var(--card-white); }
  .card-back { left: 620px; background: var(--brand-blue); }

  .wordmark {
    display: flex;
    align-items: center;
    gap: 10px;
    color: var(--brand-blue);
    font-weight: 800;
    letter-spacing: 2px;
    line-height: 1;
  }
  .card-front .wordmark {
    position: absolute;
    left: 50%; top: 50%;
    transform: translate(-50%, -50%);
    font-size: 64px;
  }
  .wordmark-square {
    width: 0.28em; height: 0.28em;
    background: var(--accent-blue);
    flex: none;
  }

  .logo-band {
    position: absolute;
    left: 0; top: 0;
    width: 156px; height: 100%;
    background: var(--card-white);
  }
  .logo-band .wordmark {
    position: absolute;
    left: 50%; top: 50%;
    transform: translate(-50%, -50%) rotate(-90deg);
    font-size: 44px;
    white-space: nowrap;
  }

  .name-tab {
    position: absolute;
    right: 0; top: 26px;
    width: 16px; height: 40px;
    background: var(--card-white);
  }
  .identity {
    position: absolute;
    right: 30px; top: 26px;
    text-align: right;
    color: var(--ink-light);
  }
  .person-name {
    font-size: 22px;
    font-weight: 700;
    letter-spacing: 0.5px;
    text-transform: uppercase;
    line-height: 1.1;
  }
  .person-role {
    font-size: 14px;
    font-weight: 400;
    line-height: 1.3;
  }
  .divider {
    position: absolute;
    right: 16px; top: 76px;
    width: 300px; height: 1px;
    background: var(--ink-light);
  }

  .contact {
    position: absolute;
    right: 18px; top: 150px;
    list-style: none;
    color: var(--ink-light);
    font-size: 12.5px;
    line-height: 1.5;
    text-align: right;
  }
  .contact li { display: flex; justify-content: flex-end; align-items: center; gap: 7px; }
  .contact .address { padding-right: 21px; }
  .contact .address-gap { margin-bottom: 14px; }
  .contact-icon { width: 14px; height: 14px; flex: none; }
</style>
</head>
<body>

  <section class="card card-front" aria-label="Card front">
    <div class="wordmark"><span class="wordmark-square"></span>TOVRIN</div>
  </section>

  <section class="card card-back" aria-label="Card back">
    <div class="logo-band">
      <div class="wordmark"><span class="wordmark-square"></span>TOVRIN</div>
    </div>

    <div class="name-tab"></div>
    <div class="identity">
      <p class="person-name">Warren Halbeck</p>
      <p class="person-role">General Manager</p>
    </div>
    <div class="divider"></div>

    <ul class="contact">
      <li class="address">87 Marrow Ave,</li>
      <li class="address address-gap">Pendlebay, QLD, 4023</li>
      <li>0472 915 348
        <svg class="contact-icon" viewBox="0 0 14 14" aria-hidden="true">
          <circle cx="7" cy="7" r="7" fill="#fff"/>
          <path d="M4.3 3.6l1.4-.4.8 1.8-.9.7c.4.9 1 1.6 1.9 2.1l.8-.8 1.8.9-.4 1.4c-3 .2-5.6-2.7-5.4-5.7z" fill="#1456a8"/>
        </svg>
      </li>
      <li>www.tovrin.com.au
        <svg class="contact-icon" viewBox="0 0 14 14" aria-hidden="true">
          <circle cx="7" cy="7" r="7" fill="#fff"/>
          <circle cx="7" cy="7" r="4.3" fill="none" stroke="#1456a8" stroke-width="0.9"/>
          <ellipse cx="7" cy="7" rx="1.8" ry="4.3" fill="none" stroke="#1456a8" stroke-width="0.9"/>
          <path d="M2.7 7h8.6" stroke="#1456a8" stroke-width="0.9"/>
        </svg>
      </li>
      <li>Warren.halbeck@tovrin.com.au
        <svg class="contact-icon" viewBox="0 0 14 14" aria-hidden="true">
          <circle cx="7" cy="7" r="7" fill="#fff"/>
          <rect x="3.3" y="4.4" width="7.4" height="5.2" fill="none" stroke="#1456a8" stroke-width="0.9"/>
          <path d="M3.3 4.4L7 7.4l3.7-3" fill="none" stroke="#1456a8" stroke-width="0.9"/>
        </svg>
      </li>
    </ul>
  </section>

</body>
</html>
```